Australian Trucking Company Requires Professional Looking Stationary

We require a professional looking stationary design that incorporates our newly designed logo.

Our business, called "Brell Haulage Contracting", provides contracting work, transport and logistics to business in Western Australia particularly with links to the mining sector.

We are a small business looking to expand and our new logo and our new stationary will help develop our brand image in our market place.

Target Market(s)

Businesses and Corporation with links to the Mining Sector

Industry/Entity Type

Small Business

Requirements
Must have
• The letterhead must have the following details:
The new logo

Text saying: "Brell Holdings Pty Ltd (ACN 582 316 907) ATF The Brell Discretionary Trust T/AS"
"ABN 71 834 209 553"
Address "P.O Box 817 Wattlegrove WA, 6958"
Phone: 08 9352 7140
Email: brellhaul@mailbox-example.com.au

The text on the letterhead should be editable as the details are likely to change in the near future. Provision should be made for a website address all though one isn't available at the moment.

The styling, layout and font text is entirely up to the designer.

```html
<!DOCTYPE html>
<html lang="en">
<head>
<meta charset="utf-8">
<title>Brell Haulage Contracting – Business Cards</title>
<link href="https://fonts.googleapis.com/css2?family=Arimo:wght@400;700&display=swap" rel="stylesheet">
<style>
  :root {
    --stage: #e9e7e4;
    --card: #ffffff;
    --red-deep: #7a0008;
    --red-mid: #9e0a12;
    --red-bright: #e21b24;
    --grey-mark: #6a6a6a;
    --grey-soft: #d4d4d4;
    --ink-light: #ffffff;
  }
  * { margin: 0; padding: 0; box-sizing: border-box; }
  html, body {
    width: 1200px; height: 1200px; overflow: hidden;
    background: var(--stage);
    font-family: "Arimo", Arial, sans-serif;
  }
  .canvas { position: relative; width: 1200px; height: 1200px; }
  .card {
    position: absolute; width: 840px; height: 480px;
    background: var(--card); overflow: hidden;
    box-shadow: 0 6px 18px rgba(0,0,0,0.18);
  }
  .card--front { left: 84px; top: 78px; }
  .card--back  { left: 284px; top: 650px; width: 842px; }
  .card__swoosh { position: absolute; inset: 0; width: 100%; height: 100%; }

  .brand { position: absolute; left: 44px; top: 30px; display: flex; align-items: center; gap: 34px; }
  .brand__mark { width: 150px; height: 150px; border-radius: 50%; background: var(--grey-mark); }
  .brand__name {
    color: var(--red-mid); font-weight: 700; font-size: 50px; line-height: 54px;
    text-transform: uppercase; letter-spacing: 1px;
  }

  .contact { position: absolute; right: 40px; top: 280px; text-align: right; color: var(--ink-light); }
  .contact__name { font-size: 32px; line-height: 40px; margin-right: 8px; margin-bottom: 12px; }
  .contact__title { font-size: 25px; letter-spacing: 2px; }
  .contact__list { list-style: none; }
  .contact__item {
    display: flex; justify-content: flex-end; align-items: center;
    font-size: 21px; line-height: 33.5px;
  }
  .contact__icon { width: 18px; height: 18px; margin-left: 18px; flex: none; }

  .scene-art { position: absolute; left: 30px; top: 0; width: 720px; height: 400px; }

  .back-info { position: absolute; right: 26px; top: 390px; text-align: right; color: var(--ink-light); }
  .back-info__web { font-size: 29px; letter-spacing: 3px; line-height: 36px; }
  .back-info__web strong { font-weight: 700; letter-spacing: 4px; }
  .back-info__legal { font-size: 18.5px; margin-top: 8px; white-space: nowrap; }
</style>
</head>
<body>
<main class="canvas">

  <section class="card card--front">
    <svg class="card__swoosh" viewBox="0 0 840 480" preserveAspectRatio="none" aria-hidden="true">
      <defs>
        <linearGradient id="frontRed" x1="0" y1="0" x2="0.3" y2="1">
          <stop offset="0" stop-color="var(--red-deep)"/>
          <stop offset="1" stop-color="#b50f19"/>
        </linearGradient>
        <linearGradient id="frontEdge" x1="0" y1="0" x2="1" y2="0">
          <stop offset="0" stop-color="var(--red-deep)"/>
          <stop offset="0.55" stop-color="var(--red-bright)"/>
          <stop offset="1" stop-color="var(--red-mid)"/>
        </linearGradient>
      </defs>
      <path d="M0,480 Q380,262 840,202 L840,480 Z" fill="url(#frontEdge)"/>
      <path d="M0,478 Q420,295 840,226 L840,480 L0,480 Z" fill="url(#frontRed)"/>
      <path d="M0,478 Q420,295 840,226" fill="none" stroke="#fff" stroke-width="3.5"/>
    </svg>

    <div class="brand">
      <div class="brand__mark"></div>
      <div class="brand__name">Brell<br>Haulage<br>Contracting</div>
    </div>

    <div class="contact">
      <p class="contact__name">Your Name / <span class="contact__title">Title</span></p>
      <ul class="contact__list">
        <li class="contact__item">08 9352 7140
          <svg class="contact__icon" viewBox="0 0 20 20"><circle cx="10" cy="10" r="8.5" fill="none" stroke="#fff" stroke-width="1.4"/><path d="M7 5.5l2 2-1 1.2c.6 1.4 1.6 2.4 3 3l1.2-1 2 2-1.4 1.6C9.8 14 6 10.2 5.8 7z" fill="#fff"/></svg>
        </li>
        <li class="contact__item">brellhaul@mailbox-example.com.au
          <svg class="contact__icon" viewBox="0 0 20 20"><rect x="2" y="5" width="16" height="11" fill="#fff"/><path d="M2 5l8 6 8-6" fill="none" stroke="#9e0a12" stroke-width="1.3"/></svg>
        </li>
        <li class="contact__item">www.brellhaulage.com
          <svg class="contact__icon" viewBox="0 0 20 20" fill="none" stroke="#fff" stroke-width="1.3"><circle cx="10" cy="10" r="8"/><ellipse cx="10" cy="10" rx="3.5" ry="8"/><path d="M2 10h16M3.5 6h13M3.5 14h13"/></svg>
        </li>
        <li class="contact__item">P.O Box 817 Wattlegrove WA, 6958
          <svg class="contact__icon" viewBox="0 0 20 20"><path d="M10 2L1.5 10h2.5v8h4.5v-5h3v5H16v-8h2.5z" fill="#fff"/></svg>
        </li>
      </ul>
    </div>
  </section>

  <section class="card card--back">
    <svg class="scene-art" viewBox="0 0 720 400" role="img" aria-label="Illustration of three semi-trailer trucks climbing the road, growing larger left to right">
      <defs>
        <linearGradient id="artGrey" x1="0" y1="1" x2="1" y2="0">
          <stop offset="0" stop-color="#bdbdbd"/>
          <stop offset="1" stop-color="#6d6d6d"/>
        </linearGradient>
      </defs>
      <path d="M30,390 L140,300 L220,320 L250,230 L450,250 L500,50 L720,0 L720,175 Q420,230 90,400 Z" fill="url(#artGrey)" opacity="0.55"/>
    </svg>

    <svg class="card__swoosh" viewBox="0 0 842 480" preserveAspectRatio="none" aria-hidden="true">
      <defs>
        <linearGradient id="backRed" x1="0" y1="0" x2="0.3" y2="1">
          <stop offset="0" stop-color="var(--red-deep)"/>
          <stop offset="1" stop-color="#b50f19"/>
        </linearGradient>
        <linearGradient id="backEdge" x1="0" y1="0" x2="1" y2="0">
          <stop offset="0" stop-color="var(--red-deep)"/>
          <stop offset="0.5" stop-color="var(--red-bright)"/>
          <stop offset="1" stop-color="var(--red-deep)"/>
        </linearGradient>
      </defs>
      <path d="M0,480 Q400,250 842,174 L842,480 Z" fill="url(#backEdge)"/>
      <path d="M0,472 Q440,292 842,222 L842,480 L0,480 Z" fill="url(#backRed)"/>
      <path d="M0,472 Q440,292 842,222" fill="none" stroke="#fff" stroke-width="5"/>
    </svg>

    <div class="back-info">
      <p class="back-info__web">www.<strong>brellhaulage</strong>.com</p>
      <p class="back-info__legal">Brell Holdings Pty Ltd (ACN 582 316 907) ATF The Brell Discretionary Trust T/AS</p>
    </div>
  </section>

</main>
</body>
</html>
```